Lush Satchel

I am developing a web site which sells preowned high end designer handbags and accessories. Some of the brands include: Varenne, Marcel Ostrand & Belmo, to name a few. I am after a luxurious and high end feel.

Some brands I like that express this feel include: Quintel, Belmo, fabcloset.com, pursepassonpaw.com

I am after a logo, business card, letterhead, with compliments, address label and envelope designs.
The business name is Lush satchel, and the website will be www.lushsatchel.com.au. I have thoughts of using LSC as a logo or LUSH satchel.com.au

I don't want a large logo, it needs to blend in with the name in some way - or may not need an image at all, if the style of the font speaks to the brand.

Thank-you
Updates

Project Deadline Extended
Reason: I would like to give designers plenty of time to be able to submit a design.

Target Market(s)

Women, aged 25-60 who are into fashion

Industry/Entity Type

Business

Requirements
Must have
• High End
Luxurious

```html
<!DOCTYPE html>
<html lang="en">
<head>
<meta charset="utf-8">
<title>Lush Satchel – Envelope Designs</title>
<link href="https://fonts.googleapis.com/css2?family=Arimo:wght@400&family=Cormorant+Garamond:ital,wght@0,500;1,500&display=swap" rel="stylesheet">
<style>
  :root {
    --crimson: #c11f42;
    --ink: #000000;
    --paper: #ffffff;
    --line: #111111;
  }
  html, body {
    margin: 0;
    padding: 0;
    overflow: hidden;
    background: var(--paper);
  }
  .sheet {
    position: relative;
    width: 1200px;
    height: 1021px;
    overflow: hidden;
    background: var(--paper);
    font-family: "Arimo", Arial, sans-serif;
    color: var(--ink);
  }
  .envelope {
    position: absolute;
    box-sizing: border-box;
    border: 2px solid var(--line);
    background: var(--paper);
    overflow: hidden;
  }
  .window {
    position: absolute;
    box-sizing: border-box;
    border: 2px solid var(--line);
    border-radius: 34px;
    background: var(--paper);
  }
  .brand-name {
    position: absolute;
    margin: 0;
    font-family: "Cormorant Garamond", Georgia, serif;
    font-weight: 500;
    font-style: italic;
    color: var(--crimson);
    white-space: nowrap;
    line-height: 1;
  }
  .brand-name--vertical {
    transform-origin: left top;
    transform: rotate(90deg);
  }
  .web-address {
    position: absolute;
    margin: 0;
    font-size: 18px;
    line-height: 1;
    white-space: nowrap;
  }
  .web-address--tiny { font-size: 6.5px; }
  .web-address--vertical {
    font-size: 6.5px;
    transform-origin: left top;
    transform: rotate(90deg);
  }
  .flap { position: absolute; display: block; }

  .env-signature { left: 0; top: 6px; width: 628px; height: 226px; }
  .env-flap      { left: 5px; top: 280px; width: 627px; height: 227px; }
  .env-bag       { left: 2px; top: 527px; width: 627px; height: 226px; }
  .env-minibag   { left: 5px; top: 786px; width: 628px; height: 226px; }
  .env-tall-a    { left: 710px; top: 0; width: 226px; height: 628px; }
  .env-tall-b    { left: 963px; top: 1px; width: 226px; height: 628px; }
</style>
</head>
<body>
<main class="sheet">

  <section class="envelope env-signature">
    <p class="brand-name" style="left:30px; top:44px; font-size:70px;">Lush Satchel</p>
    <div class="window" style="left:374px; top:132px; width:229px; height:69px;"></div>
  </section>

  <section class="envelope env-flap">
    <svg class="flap" width="627" height="130" viewBox="0 0 627 130" aria-hidden="true">
      <polygon points="0,0 627,0 327,125" fill="var(--crimson)"/>
    </svg>
    <p class="web-address" style="left:19px; top:184px;">lushsatchel.com.au</p>
  </section>

  <section class="envelope env-bag">
    <p class="brand-name" style="left:22px; top:80px; font-size:40px;">Lush Satchel</p>
    <p class="web-address" style="left:37px; top:195px;">lushsatchel.com.au</p>
    <div class="window" style="left:373px; top:131px; width:229px; height:69px;"></div>
  </section>

  <section class="envelope env-minibag">
    <p class="brand-name" style="left:36px; top:58px; font-size:13px;">Lush Satchel</p>
    <p class="web-address web-address--tiny" style="left:38px; top:99px;">lushsatchel.com.au</p>
    <div class="window" style="left:373px; top:131px; width:229px; height:69px;"></div>
  </section>

  <section class="envelope env-tall-a">
    <p class="brand-name brand-name--vertical" style="left:180px; top:20px; font-size:24px;">Lush Satchel</p>
    <p class="web-address web-address--vertical" style="left:146px; top:46px;">lushsatchel.com.au</p>
    <div class="window" style="left:24px; top:375px; width:69px; height:229px;"></div>
  </section>

  <section class="envelope env-tall-b">
    <p class="brand-name" style="left:76px; top:84px; font-size:26px;">Lush Satchel</p>
    <div class="window" style="left:22px; top:378px; width:69px; height:229px;"></div>
  </section>

</main>
</body>
</html>
```